New, modern business card for growing audiology practice

We need a new business card for our audiology practice. Our logo and website have recently changed (more modern) and we want our business cards to reflect this change.
We conduct hearing tests, perform earwax removals, and fit & dispense hearing aids to our patients. We are a family owned practice in which the owner is the one who works directly with the patient. I have attached logos in various formats to use, as well as two ideas I found on this website; as well as a scanned copy of our current logo. Good luck!

Industry/Entity Type

Business

Contact Information for Business Card

Company name: Tolvera Hearing Center
Provider name: Peter Wolstenby, Au.D. F/NSB
Phone number: (440) 683-5127
Address: 837 W. Lindell Ave. Marlow Brook, OH 44391
email: tolverahearing@postvane.com
website: tolverahearing.com

Colors
000000
aaaaaa
dbdbdb
cacaca
9bcb3c
afd23c
cadf82
b1b1b1

Requirements
Must have
• My card must include information in the "details" section. In the attached images, I found a few that I liked and I would like to model after - "brisky bouncin'" and "Sound Method Center".
• Must be horizontal.
• Must include logos provided. I uploaded them in various file formats and various ways.
• Must match logo font, if possible, if not, please get as close as you can.
Nice to have
• I really like the idea of having a color on one side with just the logo and company name and the contact information and provider name on the other side. I also really like the idea of having the main color dominating on the logo/company side with accent of that same color on the contact side of the card.
Should not have
• Must not be vertical.

```html
<!DOCTYPE html>
<html lang="en">
<head>
<meta charset="utf-8">
<title>Tolvera Hearing Center – Business Card</title>
<link rel="stylesheet" href="https://fonts.googleapis.com/css2?family=Lato:wght@400&family=Roboto:wght@400&family=Fjalla+One&display=swap">
<style>
  :root {
    --page-bg: #d9d9d9;
    --card-bg: #232323;
    --text-light: #f2f2f2;
    --brand-green: #5f9a35;
    --accent-green: #69a83a;
    --band-grey: #aaaaaa;
  }
  * { margin: 0; padding: 0; box-sizing: border-box; }
  html, body { width: 799px; height: 1200px; overflow: hidden; }
  body {
    background: var(--page-bg);
    font-family: "Roboto", sans-serif;
    position: relative;
  }
  .card {
    position: absolute;
    left: 60px;
    width: 680px;
    height: 389px;
    background: var(--card-bg);
    overflow: hidden;
    box-shadow: 0 6px 18px rgba(0,0,0,0.35);
  }
  .card--front { top: 150px; }
  .card--back { top: 660px; }

  .brand {
    position: absolute;
    display: flex;
    align-items: center;
    gap: 14px;
    font-family: "Lato", sans-serif;
    font-weight: 400;
    color: var(--text-light);
    text-transform: uppercase;
    letter-spacing: 0.5px;
    white-space: nowrap;
  }
  .brand__dot {
    width: 22px; height: 22px;
    border-radius: 50%;
    background: var(--brand-green);
    flex: none;
  }
  .card--front .brand { left: 58px; top: 150px; font-size: 38px; }
  .card--back .brand { left: 40px; top: 40px; font-size: 36px; }

  .front-web {
    position: absolute;
    left: 62px; top: 290px;
    font-size: 17px;
    letter-spacing: 5px;
    color: var(--text-light);
  }
  .front-web .domain { color: var(--brand-green); }

  .provider {
    position: absolute;
    left: 40px; top: 165px;
  }
  .provider__name {
    font-family: "Fjalla One", sans-serif;
    font-size: 25px;
    color: var(--brand-green);
    line-height: 1.1;
  }
  .provider__title {
    font-size: 15px;
    color: var(--text-light);
    margin-top: 4px;
  }

  .contact {
    position: absolute;
    left: 385px; top: 185px;
    font-size: 16px;
    color: var(--text-light);
    line-height: 1.35;
  }
  .contact__row { display: flex; align-items: center; gap: 10px; }
  .contact__row svg { flex: none; }
  .contact__address { padding-left: 26px; margin-bottom: 4px; }

  .bands { position: absolute; left: 0; top: 0; }
  .back-web {
    position: absolute;
    left: 300px; right: 0; top: 336px;
    text-align: center;
    font-size: 19px;
    color: var(--text-light);
  }
</style>
</head>
<body>

<section class="card card--front" aria-label="Card front">
  <div class="brand"><span class="brand__dot"></span>Tolvera Hearing Center</div>
  <p class="front-web">www.<span class="domain">tolverahearing</span>.com</p>
</section>

<section class="card card--back" aria-label="Card back">
  <div class="brand"><span class="brand__dot"></span>Tolvera Hearing Center</div>

  <div class="provider">
    <p class="provider__name">Peter Wolstenby, Au.D. F/NSB</p>
    <p class="provider__title">Owner - Audiologist</p>
  </div>

  <div class="contact">
    <p class="contact__address">837 W. Lindell Ave.<br>Marlow Brook, OH 44391</p>
    <p class="contact__row">
      <svg width="16" height="14" viewBox="0 0 16 14" aria-hidden="true">
        <path d="M1 4 Q8 -1 15 4 L13 6 L11 4.5 L5 4.5 L3 6 Z" fill="#69a83a"/>
        <rect x="3" y="7" width="10" height="6" rx="1" fill="#69a83a"/>
      </svg>
      (440) 683-5127
    </p>
    <p class="contact__row">
      <svg width="16" height="12" viewBox="0 0 16 12" aria-hidden="true">
        <rect x="0.5" y="0.5" width="15" height="11" fill="none" stroke="#69a83a" stroke-width="1.5"/>
        <path d="M0.5 0.5 L8 7 L15.5 0.5" fill="none" stroke="#69a83a" stroke-width="1.5"/>
      </svg>
      tolverahearing@postvane.com
    </p>
  </div>

  <svg class="bands" width="680" height="389" viewBox="0 0 680 389" aria-hidden="true">
    <polygon points="0,292 300,292 300,312 0,312" fill="var(--band-grey)"/>
    <polygon points="300,318 680,318 680,389 262,389" fill="var(--accent-green)"/>
  </svg>
  <p class="back-web">www.tolverahearing.com</p>
</section>

</body>
</html>
```